Frostvale Harborline LLC

we need a business card design

Industry/Entity Type

hvac

Contact Information for Business Card

my logo

Requirements
Must have
• my logo and same colors

```html
<!DOCTYPE html>
<html lang="en">
<head>
<meta charset="utf-8">
<title>Frostvale Harborline LLC – Business Card</title>
<link href="https://fonts.googleapis.com/css2?family=Montserrat:wght@400;500;700;800&display=swap" rel="stylesheet">
<style>
  :root{
    --stage:#3b3b3d;
    --paper:#ffffff;
    --cyan:#19a9df;
    --sun:#f6b857;
    --navy:#0b3c8f;
    --navy-deep:#072c72;
    --ink:#1f1f22;
    --brand-ink:#1a5aab;
  }
  *{box-sizing:border-box;margin:0;padding:0}
  html,body{width:1200px;height:1200px;overflow:hidden}
  body{
    background:var(--stage);
    font-family:"Montserrat",Arial,sans-serif;
    display:flex;flex-direction:column;align-items:center;justify-content:center;gap:60px;
  }
  .card{
    position:relative;width:900px;height:514px;border-radius:34px;overflow:hidden;
    box-shadow:0 18px 40px rgba(0,0,0,.45);
  }
  /* front */
  .card--front{background:var(--paper)}
  .contact{position:absolute;left:66px;top:196px}
  .contact__name{color:var(--cyan);font-weight:500;font-size:50px;letter-spacing:1px;line-height:1}
  .contact__title{color:var(--ink);font-weight:400;font-size:30px;line-height:1.1;margin-top:4px;letter-spacing:.5px}
  .contact__list{list-style:none;margin-top:14px}
  .contact__item{display:flex;align-items:flex-start;gap:16px;color:var(--ink);font-size:22px;line-height:30px}
  .contact__icon{width:24px;height:24px;flex:none;margin-top:3px}
  .contact__icon--solid{fill:var(--cyan)}
  .contact__icon--line{fill:none;stroke:var(--cyan);stroke-width:1.8}
  .brand{position:absolute;display:flex;align-items:center;gap:16px}
  .card--front .brand{right:70px;top:150px}
  .brand__dot{width:28px;height:28px;border-radius:50%;flex:none}
  .brand__name{font-weight:800;font-size:34px;line-height:1.15;letter-spacing:.5px}
  .card--front .brand__dot{background:var(--sun)}
  .card--front .brand__name{color:var(--brand-ink)}
  .band{position:absolute;left:0;right:0;bottom:0;height:22px;display:flex}
  .band__cyan{flex:0 0 63%;background:var(--cyan)}
  .band__sun{flex:1;background:var(--sun);margin-left:8px}
  /* back */
  .card--back{background:radial-gradient(ellipse at 40% 30%,var(--navy) 0%,var(--navy-deep) 100%)}
  .card--back .brand{left:50%;top:50%;transform:translate(-50%,-50%)}
  .card--back .brand__dot{background:var(--sun);width:40px;height:40px}
  .card--back .brand__name{color:var(--paper);font-size:48px}
</style>
</head>
<body>
  <section class="card card--front" aria-label="Business card front">
    <div class="brand">
      <span class="brand__dot"></span>
      <span class="brand__name">Frostvale<br>Harborline LLC</span>
    </div>
    <div class="contact">
      <p class="contact__name">FULL NAME</p>
      <p class="contact__title">TITLE</p>
      <ul class="contact__list">
        <li class="contact__item">
          <svg class="contact__icon contact__icon--solid" viewBox="0 0 24 24"><path d="M6.6 10.8a15 15 0 0 0 6.6 6.6l2.2-2.2a1 1 0 0 1 1-.25 11.4 11.4 0 0 0 3.6.6 1 1 0 0 1 1 1V20a1 1 0 0 1-1 1A17 17 0 0 1 3 4a1 1 0 0 1 1-1h3.5a1 1 0 0 1 1 1c0 1.25.2 2.45.6 3.6a1 1 0 0 1-.25 1z"/></svg>
          <span>(000) 000 0000</span>
        </li>
        <li class="contact__item">
          <svg class="contact__icon contact__icon--line" viewBox="0 0 24 24"><path d="M2 5h20v14H2z"/><path d="M2 5l10 8 10-8"/></svg>
          <span>email@company.com</span>
        </li>
        <li class="contact__item">
          <svg class="contact__icon contact__icon--line" viewBox="0 0 24 24"><circle cx="12" cy="12" r="10"/><path d="M2 12h20M12 2c3 3 3 17 0 20M12 2c-3 3-3 17 0 20"/></svg>
          <span>www.company.com</span>
        </li>
        <li class="contact__item">
          <svg class="contact__icon contact__icon--solid" viewBox="0 0 24 24"><path d="M12 2a7 7 0 0 0-7 7c0 5 7 13 7 13s7-8 7-13a7 7 0 0 0-7-7zm0 9.5A2.5 2.5 0 1 1 12 6.5a2.5 2.5 0 0 1 0 5z"/></svg>
          <span>123 Name Street, 000<br>Your City, 00000-000</span>
        </li>
      </ul>
    </div>
    <div class="band"><span class="band__cyan"></span><span class="band__sun"></span></div>
  </section>

  <section class="card card--back" aria-label="Business card back">
    <div class="brand">
      <span class="brand__dot"></span>
      <span class="brand__name">Frostvale<br>Harborline LLC</span>
    </div>
  </section>
</body>
</html>
```